New Modern Wix Website Design

We are NOT your typical electrical/home improvement contractor, so we need our website updated. We already have a logo for each division.
We provided a neutral logo with a hard hat, a logo for the home improvement, and a logo for the electrical division. (if we can implement all 3 logos will be great but at least the 2 for the divisions must be used.

We looking for a website that a 10-year-old can understand, our target audience is the new young generation that wants innovations in their properties, smart homes, cool smart things/gadgets. So we need a website that is fun, simple, eye-catching. (we don't want to appear TOO serious and boring)
NO GENERIC WEBSITES SO MUST BE VERY CREATIVE!!!

We want to be able to share google reviews, a contact box, business hours, our services, etc...

current website kelvantrio.example

Target Market(s)

Contractors in different trades.

Industry/Entity Type

Construction

Colors
FFC000
F8CF3A
FAE287
FDF2CF
FEFAEE

Requirements
Must have
• Modern upmarket look and feel
Nice to have
• already attached supporting images.
Should not have
• basic typical construction boring and depressing look and feel.

```html
<!DOCTYPE html>
<html lang="en">
<head>
<meta charset="UTF-8">
<title>Kelvantrio — Open Positions</title>
<link href="https://fonts.googleapis.com/css2?family=Poppins:wght@400;500;600&display=swap" rel="stylesheet">
<style>
:root{
  --amber:#FFC000;
  --gold:#F8CF3A;
  --sand:#FAE287;
  --cream:#FDF2CF;
  --ivory:#FEFAEE;
  --ink:#111111;
  --line:#c9bfa3;
  --field:#ffffff;
  --muted:#777;
}
*{box-sizing:border-box;margin:0;padding:0}
html,body{width:781px;height:1200px;overflow:hidden;background:#fff;font-family:'Poppins',sans-serif;color:var(--ink)}
.page{position:absolute;left:78px;top:36px;width:625px;height:1128px;background:var(--cream);border:1px solid #8a8a8a;overflow:hidden}
.abs{position:absolute}
.waves{position:absolute;left:0;top:0}
.brand{display:flex;align-items:center;gap:4px;font-weight:600;font-size:9px;letter-spacing:.3px}
.brand-dot{width:8px;height:8px;border-radius:50%;background:var(--amber)}
.nav{display:flex;gap:0;font-size:7.5px;top:18px}
.nav a{position:absolute;color:var(--ink);text-decoration:none;white-space:nowrap}
.nav .active{color:var(--amber);text-decoration:underline wavy var(--amber);text-underline-offset:2px}
.nav-more{position:absolute;font-size:9px;letter-spacing:1px;font-weight:600}
.btn-contact{left:523px;top:13px;width:62px;height:20px;background:var(--amber);color:#fff;font-size:7.5px;display:flex;align-items:center;justify-content:center}
.illustration{left:-2px;top:60px;width:129px;height:137px;background:var(--ivory);border-radius:20px 60px 70px 40px}
.title{left:0;width:625px;top:88px;text-align:center;font-size:20px;font-weight:500}
.tag{left:149px;top:127px;width:327px;height:18px;background:var(--amber);font-size:10.3px;font-weight:500;display:flex;align-items:center;justify-content:center}
.col{left:132px;width:362px}
.section-head{display:flex;align-items:center;gap:6px;font-size:10px;font-weight:500;height:22px}
.rule{height:1px;background:var(--line)}
.para{font-size:7.3px;line-height:11px}
.label{font-size:7px;font-weight:500}
.input{height:16px;background:var(--field);border:1px solid #8a8a8a;border-radius:3px;font-size:5.5px;color:var(--muted);padding-left:12px;display:flex;align-items:center}
.select{justify-content:space-between;padding-right:8px}
.question{font-size:5.8px}
.question b{color:#d33;font-weight:400}
.radio{display:flex;align-items:center;gap:4px;font-size:5.8px}
.radio i{width:6px;height:6px;border:1px solid #777;border-radius:50%}
.textarea{height:59px;align-items:flex-start;padding-top:6px}
.submit{height:22px;background:var(--ink);color:#fff;font-size:7px;font-weight:600;display:flex;align-items:center;justify-content:center}
.newsletter{left:86px;top:750px;width:453px;height:114px;background:var(--sand);border-radius:6px;box-shadow:0 2px 6px rgba(0,0,0,.06)}
.newsletter h2{position:absolute;top:14px;width:100%;text-align:center;font-size:20px;font-weight:500}
.newsletter p{position:absolute;top:47px;width:100%;text-align:center;font-size:7.3px;font-weight:500}
.nl-input{position:absolute;left:40px;top:64px;width:178px;height:30px;background:#fff;font-size:6px;color:#999;padding-left:13px;display:flex;align-items:center}
.nl-btn{position:absolute;left:235px;top:64px;width:178px;height:30px;background:var(--amber);font-size:7px;font-weight:600;display:flex;align-items:center;justify-content:center}
.foot-head{font-size:9.5px;font-weight:500}
.foot-list{list-style:none;font-size:7.2px;line-height:17px}
.map{left:407px;top:997px;width:178px;height:98px;background:linear-gradient(135deg,#e7e3dc,#d8d4cc 60%,#e9dfcf)}
.social{left:216px;top:1064px;width:8px;height:8px;background:var(--amber)}
.copy{left:0;width:625px;top:1107px;text-align:center;font-size:5.5px;color:#555}
</style>
</head>
<body>
<div class="page">
  <svg class="waves" width="625" height="1128" viewBox="0 0 625 1128" aria-hidden="true">
    <path d="M0 812 Q150 800 300 812 T625 798 V1128 H0 Z" fill="var(--ivory)"/>
  </svg>

  <div class="abs brand" style="left:39px;top:20px"><span class="brand-dot"></span>KELVANTRIO</div>

  <nav class="abs nav" style="left:0;top:18px;width:625px;height:12px">
    <a style="left:256px">Home</a>
    <a style="left:298px">Our Services</a>
    <a class="active" style="left:364px">Job Opportunity</a>
    <a style="left:444px">About</a>
    <span class="nav-more" style="left:486px;top:-3px">•••</span>
  </nav>
  <div class="abs btn-contact">Contact us</div>

  <div class="abs illustration" role="img" aria-label="Line illustration of hands filling out a form next to a coffee cup"></div>

  <h1 class="abs title">Open Positions</h1>
  <div class="abs tag">Independent Journeyman Electricians and Apprentice/Helpers</div>

  <div class="abs col" style="top:184px">
    <div class="section-head">
      <svg width="20" height="20" viewBox="0 0 20 20"><rect x="2" y="2" width="13" height="16" fill="none" stroke="#333" stroke-width="1"/><path d="M5 6h7M5 9h7M5 12h5" stroke="#333"/><path d="M17 8 11 17" stroke="var(--amber)" stroke-width="2"/></svg>
      Description
    </div>
  </div>
  <div class="abs col rule" style="top:212px"></div>
  <p class="abs col para" style="top:227px">Kelvantrio is hiring Independent Journeyman Electricians, with at least 5 years of experience in both residential and commercial.<br>Pays up to $120k a year.<br><br>To begin the application, please fill out the form below and include as much detail as possible for consideration. We'll contact you with any questions and/or to schedule an interview.</p>

  <div class="abs col" style="top:307px">
    <div class="section-head">
      <svg width="20" height="20" viewBox="0 0 20 20"><rect x="1" y="3" width="14" height="12" rx="2" fill="none" stroke="#333"/><path d="M4 7h3M4 10h3M9 7h3" stroke="#333"/><circle cx="15" cy="14" r="4" fill="none" stroke="#333"/><circle cx="15" cy="14" r="2" fill="var(--amber)"/></svg>
      personal Information
    </div>
  </div>
  <div class="abs col rule" style="top:338px"></div>

  <div class="abs label" style="left:132px;top:353px">First name</div>
  <div class="abs label" style="left:327px;top:353px">Last name</div>
  <div class="abs input" style="left:132px;top:366px;width:166px">John</div>
  <div class="abs input" style="left:327px;top:366px;width:167px">Doe</div>
  <div class="abs label" style="left:132px;top:389px">Email</div>
  <div class="abs col input" style="top:402px">Johndoe@gmail.com</div>
  <div class="abs label" style="left:132px;top:425px">Phone number</div>
  <div class="abs col input" style="top:439px">033 456784</div>

  <div class="abs col" style="top:471px">
    <div class="section-head">
      <svg width="20" height="20" viewBox="0 0 20 20"><rect x="5" y="1" width="12" height="15" rx="1" fill="none" stroke="#333"/><path d="M8 5h6M8 8h6" stroke="#333"/><path d="M2 18 9 11" stroke="var(--amber)" stroke-width="2"/></svg>
      Details
    </div>
  </div>
  <div class="abs col rule" style="top:500px"></div>

  <div class="abs col input select" style="top:513px">Select Your Job position
    <svg width="8" height="5" viewBox="0 0 8 5"><path d="M1 1l3 3 3-3" fill="none" stroke="#333"/></svg>
  </div>
  <div class="abs col input" style="top:536px">How many years of experience you have for this type of job?</div>
  <div class="abs question" style="left:132px;top:558px">Are you acrophobic? (afraid of heights)<b>*</b></div>
  <div class="abs radio" style="left:132px;top:572px"><i></i>Yes</div>
  <div class="abs radio" style="left:132px;top:582px"><i></i>No</div>
  <div class="abs col input textarea" style="top:596px">Do you have any additional details</div>
  <div class="abs col submit" style="top:679px">SUBMIT</div>

  <section class="abs newsletter">
    <h2>Join Our Newslatter</h2>
    <p>Join to get our news as we publish them</p>
    <div class="nl-input">John@gmail.com</div>
    <div class="nl-btn">SIGN UP</div>
  </section>

  <div class="abs brand" style="left:39px;top:900px"><span class="brand-dot"></span>KELVANTRIO</div>

  <h3 class="abs foot-head" style="left:39px;top:965px">Quick Links</h3>
  <ul class="abs foot-list" style="left:39px;top:989px">
    <li>Home</li><li>Our Services</li><li>Job Opportunity</li><li>About</li>
  </ul>

  <h3 class="abs foot-head" style="left:216px;top:965px">Contact us</h3>
  <ul class="abs foot-list" style="left:216px;top:989px">
    <li>info@kelvantrio.example</li><li>P +1 (555) 014-2290</li><li>F +1 (555) 014-2290</li><li>Brookvale, PA 10000</li>
  </ul>
  <div class="abs social"></div>

  <h3 class="abs foot-head" style="left:407px;top:965px">Our Locations</h3>
  <div class="abs map" role="img" aria-label="Street map showing the office location"></div>

  <div class="abs copy">©2021 by Kelvantrio ®</div>
</div>
</body>
</html>
```